Website for software company "velora"

We need a website for our software company/startup named "velora". We are developing several products (currently 3 standard-software products) which are all in different sectors, but all our products are available for Laptops/PC/Mobile Phones/Tablets, ... We do also create custom software and support our customers with consulting to optimize their processes.
We already have a Logo which you can find in the attached files.
We are a young team of 4 members (two founders and 2 employees).

To get an idea of our products -> the first one is a planning software for healthcare organizations (eg. BlueHaven, firebrigade, pharmacy), the second one is a booking software for sport clubs and the third one is a competition software for sports hunting. You see very diverse. Include or ignore this info of our products as you like.

The design has to be a bootstrap 4 (or higher) design. We have licenced FontAwesome as iconset. Responsive design should come without saying.

• Starting page, product pages, news section, contact, team, services

```html
<!DOCTYPE html>
<html lang="en">
<head>
<meta charset="utf-8">
<title>velora – Software &amp; Consulting</title>
<link rel="stylesheet" href="https://fonts.googleapis.com/css2?family=Montserrat:wght@300;400;500;600;700;800&display=swap">
<style>
:root{
  --orange:#ee7a2a;
  --orange-dark:#e06a1c;
  --navy:#252b37;
  --navy-deep:#1d2330;
  --ink:#2b2b2b;
  --muted:#5d5d5d;
  --light:#eef0f3;
  --white:#ffffff;
  --line:#d9dce1;
}
*{box-sizing:border-box;margin:0;padding:0}
html,body{width:1200px;height:4515px;overflow:hidden}
body{font-family:'Montserrat',sans-serif;color:var(--ink);background:var(--white);position:relative}
.abs{position:absolute}
.btn-outline{position:absolute;display:flex;align-items:center;justify-content:center;border:2px solid var(--orange);border-radius:22px;color:var(--orange);font-size:12px;font-weight:600;letter-spacing:.5px;text-transform:uppercase;background:transparent}
.btn-solid{position:absolute;display:flex;align-items:center;justify-content:center;border-radius:24px;background:var(--orange);color:var(--white);font-size:13px;font-weight:600;text-transform:uppercase}
.brand{font-weight:700;font-size:38px;letter-spacing:1px;text-transform:uppercase;color:var(--navy);display:flex;align-items:center;gap:10px}
.brand .dot{width:16px;height:16px;background:var(--orange)}

/* header */
.site-header{position:absolute;left:0;top:0;width:1200px;height:82px;background:var(--white)}
.site-header .brand{position:absolute;left:112px;top:18px}
.main-nav{position:absolute;top:33px;left:0;width:100%;font-size:12px;font-weight:600;color:var(--navy)}
.main-nav span{position:absolute;text-transform:uppercase}
.main-nav .active{color:var(--orange)}
.main-nav .active::after{content:"";position:absolute;left:0;right:0;bottom:-10px;height:2px;background:var(--orange)}
.main-nav .nav-contact{left:958px;top:-9px;width:126px;height:35px}

/* hero */
.hero{position:absolute;left:0;top:82px;width:1200px;height:628px;overflow:hidden}
.hero-photo{position:absolute;inset:0;background:linear-gradient(100deg,#1c2a3f 0%,#253b55 40%,#2f5a80 70%,#1c2d44 100%)}
.hero-shade{position:absolute;inset:0;background:linear-gradient(90deg,rgba(20,25,35,.75) 0%,rgba(20,25,35,.45) 45%,rgba(20,25,35,0) 70%)}
.hero h1{position:absolute;left:109px;top:180px;color:var(--white);font-size:37px;line-height:40px;font-weight:700;text-transform:uppercase}
.hero h1 .thin{font-weight:300}
.hero p{position:absolute;left:112px;top:322px;width:420px;color:var(--white);font-size:15px;line-height:21px}
.hero .btn-solid{left:112px;top:382px;width:168px;height:48px;font-size:14px}
.hero-arrow{position:absolute;top:235px}

/* about */
.about{position:absolute;left:0;top:710px;width:1200px;height:381px}
.eyebrow{position:absolute;left:140px;top:104px;font-size:11px;color:var(--orange);text-transform:uppercase;letter-spacing:.5px}
.about h2{position:absolute;left:136px;top:122px;font-size:44px;line-height:44px;font-weight:300;color:var(--navy);text-transform:uppercase}
.about h2 b{font-weight:800;display:block}
.about .rule{position:absolute;left:138px;top:218px;width:60px;height:3px;background:var(--orange)}
.about .mark{position:absolute;left:377px;top:99px;width:145px;height:172px;background:var(--orange)}
.about p{position:absolute;left:578px;top:108px;width:500px;font-size:14px;line-height:27px;color:var(--muted)}
.about .btn-outline{left:575px;top:233px;width:138px;height:42px}

/* software */
.software{position:absolute;left:0;top:1091px;width:1200px;height:1376px;background:var(--light)}
.section-title{font-size:35px;font-weight:300;color:var(--navy);text-transform:uppercase}
.section-title b{font-weight:800}
.software .section-title{position:absolute;left:0;width:1200px;top:58px;text-align:center}
.software .title-rule{position:absolute;left:576px;top:106px;width:56px;height:3px;background:var(--orange)}
.product{position:absolute;left:144px;width:951px;height:371px}
.product .cell{position:absolute;top:0;height:371px}
.product .cell-a{left:0;width:474px}
.product .cell-b{left:474px;width:477px}
.product h3{position:absolute;left:61px;top:86px;font-size:22px;font-weight:700;color:var(--navy);text-transform:uppercase}
.product h3 span{color:var(--orange)}
.product p{position:absolute;left:61px;top:128px;width:370px;font-size:13.5px;line-height:23px;color:var(--ink)}
.product .btn-outline{left:57px;top:265px;width:144px;height:40px}
.device{position:absolute}
.icon-badge{position:absolute;width:60px;height:60px;border-radius:50%;display:flex;align-items:center;justify-content:center;z-index:2}

/* services */
.services{position:absolute;left:0;top:2467px;width:1200px;height:569px;background:var(--navy)}
.services .section-title{position:absolute;left:142px;top:120px}
.services p{position:absolute;left:140px;width:350px;font-size:15px;line-height:27px;color:#e5e7eb}
.services .btn-outline{left:137px;top:389px;width:138px;height:42px;color:var(--white)}

/* news */
.news{position:absolute;left:0;top:3036px;width:1200px;height:622px}
.news .section-title{position:absolute;left:141px;top:72px}
.news-feature{position:absolute;left:140px;top:153px;width:470px;height:371px}
.news-feature .photo{position:absolute;inset:0;background:linear-gradient(160deg,#3a4a40 0%,#4d6455 35%,#2e3a40 70%,#1e262c 100%)}
.date-tag{position:absolute;background:var(--orange);color:var(--white);font-size:11px;font-weight:600;padding:4px 12px;text-transform:uppercase}
.news-feature .date-tag{left:36px;top:268px}
.news-feature h4{position:absolute;left:36px;top:302px;width:420px;color:var(--white);font-size:17px;line-height:22px;font-weight:700}
.news-card{position:absolute;left:618px;width:436px;height:177px;border:1px solid var(--line);background:var(--white)}
.news-card .photo{position:absolute;left:0;top:0;width:209px;height:100%}
.news-card .date-tag{left:229px;top:31px;font-size:10px;padding:3px 12px}
.news-card h5{position:absolute;left:229px;top:62px;font-size:12.5px;font-weight:700;color:var(--navy)}
.news-card p{position:absolute;left:229px;top:86px;width:200px;font-size:11px;line-height:20px;color:var(--muted)}

/* contact */
.contact{position:absolute;left:0;top:3658px;width:1200px;height:485px;overflow:hidden}
.contact .mark{position:absolute;left:132px;top:103px;width:26px;height:30px;background:var(--white)}
.contact h2{position:absolute;left:130px;top:148px;color:var(--white);font-size:26px;line-height:30px;font-weight:300;text-transform:uppercase}
.contact h2 b{font-weight:700;display:block}
.contact p{position:absolute;left:130px;top:254px;width:350px;color:var(--white);font-size:14px;line-height:24px}
.contact .btn-dark{position:absolute;left:130px;top:321px;width:168px;height:45px;border-radius:24px;background:var(--navy);color:var(--white);font-size:13px;font-weight:600;display:flex;align-items:center;justify-content:center;text-transform:uppercase}

/* footer */
.site-footer{position:absolute;left:0;top:4143px;width:1200px;height:372px;background:var(--white)}
.site-footer .brand{position:absolute;left:140px;top:70px;font-size:36px}
.site-footer .about-text{position:absolute;left:138px;top:130px;width:230px;font-size:10.5px;line-height:16px;color:var(--muted)}
.foot-col{position:absolute;top:74px}
.foot-col h6{font-size:12px;font-weight:700;color:var(--navy);text-transform:uppercase;position:relative;padding-left:16px}
.foot-col h6::before{content:"";position:absolute;left:0;top:2px;border-left:6px solid var(--navy);border-top:5px solid transparent;border-bottom:5px solid transparent}
.foot-col ul{list-style:none;margin-top:16px;padding-left:16px}
.foot-col li{font-size:12px;color:var(--muted);line-height:28.5px}
.divider{position:absolute;top:27px;width:1px;height:193px;background:var(--line)}
.socials{display:flex;gap:6px;margin-top:18px;padding-left:18px}
.socials span{width:29px;height:29px;border-radius:50%;background:var(--navy)}
.socials span:first-child{background:var(--orange)}
.copyright-rule{position:absolute;left:0;top:298px;width:1200px;height:1px;background:var(--line)}
.copyright{position:absolute;left:0;top:315px;width:1200px;text-align:center;font-size:10.5px;color:var(--muted)}
</style>
</head>
<body>

<header class="site-header">
  <div class="brand"><span class="dot"></span>velora</div>
  <nav class="main-nav">
    <span class="active" style="left:420px">Product</span>
    <span style="left:544px">Services</span>
    <span style="left:667px">News</span>
    <span style="left:766px">Team</span>
    <span style="left:862px">About</span>
    <span class="btn-solid nav-contact">Contact</span>
  </nav>
</header>

<section class="hero">
  <div class="hero-photo" role="img" aria-label="Photo of a developer at a desk with several monitors in a server room"></div>
  <div class="hero-shade"></div>
  <svg class="hero-arrow" style="left:34px" width="34" height="60" viewBox="0 0 34 60"><polyline points="30,2 4,30 30,58" fill="none" stroke="#fff" stroke-width="2"/></svg>
  <svg class="hero-arrow" style="left:1140px" width="34" height="60" viewBox="0 0 34 60"><polyline points="4,2 30,30 4,58" fill="none" stroke="#fff" stroke-width="2"/></svg>
  <h1><span class="thin">We help customer</span><br>to optimize their<br>processes</h1>
  <p>Lorem ipsum dolor sit amet, consectetur adipiscing elit, sed do eiusmod tempor incididunt.</p>
  <span class="btn-solid">Learn more</span>
</section>

<section class="about">
  <div class="eyebrow">Who we are</div>
  <h2>About<b>velora</b></h2>
  <div class="rule"></div>
  <div class="mark"></div>
  <p>Lorem Ipsum is simply dummy text of the printing and typesetting industry. Lorem Ipsum has been the industry's standard dummy text ever since the 1500s, when an unknown printer took a galley of type and scrambled it to make a type specimen book.</p>
  <span class="btn-outline">Learn more</span>
</section>

<section class="software">
  <h2 class="section-title">Our <b>software</b></h2>
  <div class="title-rule"></div>

  <article class="product" style="top:165px">
    <div class="cell cell-a" style="background:var(--white)">
      <h3><span>Planning</span> software</h3>
      <p>Lorem Ipsum is simply dummy text of the printing and typesetting industry. Lorem Ipsum has been the industry's standard dummy text ever since the 1500s, when an unknown printer took a galley of type and scrambled it to make a type specimen book.</p>
      <span class="btn-outline">Learn more</span>
    </div>
    <div class="cell cell-b" style="background:var(--navy)">
      <div class="device" style="left:73px;top:70px;width:332px;height:236px;border-radius:8px;background:linear-gradient(180deg,#f4f6f9,#dfe4ec)" role="img" aria-label="Laptop showing the planning software dashboard"></div>
    </div>
    <div class="icon-badge" style="left:443px;top:137px;background:var(--orange)">
      <svg width="26" height="30" viewBox="0 0 26 30"><rect x="2" y="2" width="22" height="26" rx="2" fill="none" stroke="#fff" stroke-width="2"/><line x1="7" y1="10" x2="19" y2="10" stroke="#fff" stroke-width="2"/><line x1="7" y1="15" x2="19" y2="15" stroke="#fff" stroke-width="2"/><line x1="7" y1="20" x2="15" y2="20" stroke="#fff" stroke-width="2"/></svg>
    </div>
  </article>

  <article class="product" style="top:537px">
    <div class="cell cell-a" style="background:var(--orange)">
      <div class="device" style="left:63px;top:56px;width:345px;height:260px;border-radius:8px;background:linear-gradient(180deg,#eef2f8,#d7deea)" role="img" aria-label="Tablet and phone showing the booking software"></div>
    </div>
    <div class="cell cell-b" style="background:var(--white)">
      <h3><span>Booking</span> software</h3>
      <p>Lorem Ipsum is simply dummy text of the printing and typesetting industry. Lorem Ipsum has been the industry's standard dummy text ever since the 1500s, when an unknown printer took a galley of type and scrambled it to make a type specimen book.</p>
      <span class="btn-outline">Learn more</span>
    </div>
    <div class="icon-badge" style="left:443px;top:135px;background:var(--navy)">
      <svg width="30" height="30" viewBox="0 0 30 30"><circle cx="15" cy="15" r="12" fill="none" stroke="#fff" stroke-width="2"/><polyline points="9,15 13,19 21,11" fill="none" stroke="#fff" stroke-width="2"/></svg>
    </div>
  </article>

  <article class="product" style="top:906px">
    <div class="cell cell-a" style="background:var(--white)">
      <h3><span>Competition</span> software</h3>
      <p>Lorem Ipsum is simply dummy text of the printing and typesetting industry. Lorem Ipsum has been the industry's standard dummy text ever since the 1500s, when an unknown printer took a galley of type and scrambled it to make a type specimen book.</p>
      <span class="btn-outline">Learn more</span>
    </div>
    <div class="cell cell-b" style="background:#c5c8cd">
      <div class="device" style="left:45px;top:70px;width:395px;height:226px;border-radius:8px;background:linear-gradient(180deg,#f4f6f9,#dfe4ec)" role="img" aria-label="Laptop showing the competition software dashboard"></div>
    </div>
    <div class="icon-badge" style="left:443px;top:144px;background:var(--orange)">
      <svg width="30" height="28" viewBox="0 0 30 28"><rect x="2" y="4" width="26" height="22" rx="2" fill="none" stroke="#fff" stroke-width="2"/><line x1="2" y1="10" x2="28" y2="10" stroke="#fff" stroke-width="2"/><rect x="7" y="14" width="4" height="3" fill="#fff"/><rect x="13" y="14" width="4" height="3" fill="#fff"/><rect x="19" y="14" width="4" height="3" fill="#fff"/><rect x="7" y="19" width="4" height="3" fill="#fff"/><rect x="13" y="19" width="4" height="3" fill="#fff"/></svg>
    </div>
  </article>
</section>

<section class="services">
  <svg class="abs" style="left:0;top:0" width="1200" height="569" viewBox="0 0 1200 569">
    <polygon points="690,0 722,0 562,300 722,569 690,569 530,300" fill="#ee7a2a"/>
  </svg>
  <div class="abs" style="left:0;top:0;width:1200px;height:569px;clip-path:polygon(712px 0,1200px 0,1200px 569px,712px 569px,552px 300px);background:linear-gradient(120deg,#7a4a28 0%,#a8693a 30%,#3f4a5a 65%,#1e3a55 100%)" role="img" aria-label="Photo of a team looking at code on a large screen"></div>
  <h2 class="section-title" style="color:var(--white)">Our <b>services</b></h2>
  <p style="top:182px">Lorem Ipsum is simply dummy text of the printing and typesetting industry.</p>
  <p style="top:250px">Lorem Ipsum has been the industry's standard dummy text ever since the 1500s, when an unknown printer took a galley of type and scrambled it to make a type specimen book.</p>
  <span class="btn-outline">Learn more</span>
</section>

<section class="news">
  <h2 class="section-title">Latest <b>news</b></h2>
  <article class="news-feature">
    <div class="photo" role="img" aria-label="Photo of a desk with monitors and plants in an office"></div>
    <span class="date-tag">28 May 2021</span>
    <h4>Lorem ipsum dolor sit amet, consectetur adipiscing elit, sed do eiusmod tempor</h4>
  </article>
  <article class="news-card" style="top:153px">
    <div class="photo" style="background:linear-gradient(135deg,#3a4350,#6b7584 55%,#2a313c)" role="img" aria-label="Photo of hands typing on a laptop with code on screen"></div>
    <span class="date-tag">19 May 2021</span>
    <h5>Lorem ipsum dolor sit</h5>
    <p>Duis aute irure dolor in reprehenderit in voluptate velit esse cillum dolore eu fugiat</p>
  </article>
  <article class="news-card" style="top:345px">
    <div class="photo" style="background:linear-gradient(135deg,#12325a,#2a5f9a 55%,#0e2340)" role="img" aria-label="Photo of a developer working at monitors in a blue-lit room"></div>
    <span class="date-tag">18 May 2021</span>
    <h5>Lorem ipsum dolor sit</h5>
    <p>Duis aute irure dolor in reprehenderit in voluptate velit esse cillum dolore eu fugiat</p>
  </article>
</section>

<section class="contact">
  <div class="abs" style="left:0;top:0;width:1200px;height:485px;background:linear-gradient(120deg,#4a4f58 0%,#7c7468 40%,#3b4452 75%,#2a2f38 100%)" role="img" aria-label="Photo of two colleagues reviewing a project at a computer"></div>
  <svg class="abs" style="left:0;top:0" width="1200" height="485" viewBox="0 0 1200 485"><polygon points="0,0 666,0 499,485 0,485" fill="#ee7a2a"/></svg>
  <div class="mark"></div>
  <h2><b>Contact us</b>Do you want to start<br>development&nbsp; project.</h2>
  <p>Lorem ipsum dolor sit amet, consectetur adipiscing elit, sed do eiusmod temp+</p>
  <span class="btn-dark">Contact us</span>
</section>

<footer class="site-footer">
  <div class="brand"><span class="dot"></span>velora</div>
  <p class="about-text">Lorem ipsum dolor sit amet, consectetur adipiscing elit, sed do eiusmod tempor incididunt ut labore et dolore</p>
  <div class="divider" style="left:433px"></div>
  <div class="divider" style="left:674px"></div>
  <div class="divider" style="left:897px"></div>
  <div class="foot-col" style="left:436px">
    <h6>Navigation</h6>
    <ul><li>About Us</li><li>Products</li><li>Services</li><li>Contact Us</li></ul>
  </div>
  <div class="foot-col" style="left:676px">
    <h6>Resources</h6>
    <ul><li>News</li><li>Team</li><li>Privacy Policy</li></ul>
  </div>
  <div class="foot-col" style="left:896px">
    <h6>Follow us</h6>
    <div class="socials"><span></span><span></span><span></span><span></span></div>
  </div>
  <div class="copyright-rule"></div>
  <div class="copyright">© 2022 velora &nbsp;| All Rights Reserved</div>
</footer>

</body>
</html>
```